Mindfulness School for Children -- Business Cards

We're looking for business cards for our school directors and owners. We're a mindfulness school for children called little lanterns. Attached are our logos/icons.

```html
<!DOCTYPE html>
<html lang="en">
<head>
<meta charset="utf-8">
<title>little lanterns — Business Cards</title>
<link rel="stylesheet" href="https://fonts.googleapis.com/css2?family=Alegreya:wght@400&family=Karla:wght@400&display=swap">
<style>
  :root {
    --backdrop: #2a2b2e;
    --card-white: #f7f7f5;
    --card-black: #151516;
    --pattern-tone: #1f1f21;
    --teal: #4aaec6;
    --teal-deep: #3a9bb4;
    --sage: #5fb092;
    --ink-light: #ffffff;
  }
  * { box-sizing: border-box; margin: 0; padding: 0; }
  html, body {
    width: 1200px; height: 874px; overflow: hidden;
    background: var(--backdrop);
  }
  .sheet {
    width: 1200px; height: 874px;
    display: flex; flex-direction: column; align-items: center; justify-content: center;
    gap: 56px;
  }
  .card {
    position: relative;
    width: 600px; height: 343px;
    border-radius: 22px;
    overflow: hidden;
  }
  /* Back side */
  .card--back { background: var(--card-black); }
  .card__pattern {
    position: absolute; inset: 0;
    background: radial-gradient(ellipse at 40% 35%, #242426 0%, var(--pattern-tone) 55%, var(--card-black) 100%);
  }
  .card__back-mark {
    position: absolute; right: 34px; bottom: 30px;
    display: flex; align-items: center; gap: 10px;
    font-family: "Alegreya", serif; font-size: 22px; color: var(--teal);
  }
  .mark-dot {
    width: 14px; height: 14px; border-radius: 50%; background: var(--teal);
  }
  /* Front side */
  .card--front { background: var(--card-white); }
  .brand {
    position: absolute; left: 40px; top: 46px;
    display: flex; align-items: center; gap: 12px;
    font-family: "Alegreya", serif; font-size: 44px; line-height: 1;
    color: var(--teal-deep);
  }
  .brand .mark-dot { width: 16px; height: 16px; }
  .person { position: absolute; left: 44px; top: 128px; }
  .person__name {
    font-family: "Alegreya", serif; font-size: 30px; color: var(--teal); line-height: 1;
  }
  .person__role {
    font-family: "Karla", sans-serif; font-size: 13px; color: var(--sage);
    letter-spacing: 0.04em; margin-top: 4px;
  }
  .swoosh { position: absolute; inset: 0; }
  .contact {
    position: absolute; right: 34px; bottom: 26px;
    font-family: "Karla", sans-serif; font-size: 15px; line-height: 1.35;
    color: var(--ink-light);
    display: flex; flex-direction: column; align-items: flex-end; gap: 6px;
  }
  .contact__row { display: flex; align-items: center; gap: 10px; text-align: right; }
  .contact__icon { width: 13px; height: 13px; flex: none; }
</style>
</head>
<body>
<main class="sheet">
  <section class="card card--back" aria-label="Card back">
    <div class="card__pattern" role="img" aria-label="Tone-on-tone black floral leaf pattern"></div>
    <div class="card__back-mark"><span class="mark-dot"></span>little lanterns</div>
  </section>

  <section class="card card--front" aria-label="Card front">
    <svg class="swoosh" viewBox="0 0 600 343" preserveAspectRatio="none" aria-hidden="true">
      <path d="M100 343 C 160 225, 300 168, 600 162 L 600 343 Z" fill="var(--teal)"/>
      <path d="M80 343 C 145 215, 280 156, 470 158 C 300 163, 165 225, 100 343 Z" fill="var(--sage)"/>
    </svg>

    <div class="brand"><span>little lanterns</span><span class="mark-dot"></span></div>

    <div class="person">
      <p class="person__name">Daniel Reyes</p>
      <p class="person__role">President</p>
    </div>

    <div class="contact">
      <div class="contact__row">
        <span>1420 Willow Creek Road<br>Juneau, Alaska 99801</span>
        <svg class="contact__icon" viewBox="0 0 12 12" aria-hidden="true"><path d="M6 1a3.5 3.5 0 0 0-3.5 3.5C2.5 7 6 11 6 11s3.5-4 3.5-6.5A3.5 3.5 0 0 0 6 1zm0 5a1.4 1.4 0 1 1 0-2.8A1.4 1.4 0 0 1 6 6z" fill="#fff"/></svg>
      </div>
      <div class="contact__row">
        <span>555-214-7730</span>
        <svg class="contact__icon" viewBox="0 0 12 12" aria-hidden="true"><path d="M3 1l2 2.4-1 1.4a6 6 0 0 0 3.2 3.2l1.4-1L11 9l-1 2C5.5 11 1 6.5 1 2z" fill="#fff"/></svg>
      </div>
      <div class="contact__row">
        <span>name@littlelanterns.com</span>
        <svg class="contact__icon" viewBox="0 0 12 12" aria-hidden="true"><rect x="1" y="2.5" width="10" height="7" rx="1" fill="#fff"/><path d="M1.5 3l4.5 3.5L10.5 3" stroke="var(--teal)" fill="none"/></svg>
      </div>
      <div class="contact__row">
        <span>littlelanterns.com</span>
        <svg class="contact__icon" viewBox="0 0 12 12" aria-hidden="true"><circle cx="6" cy="6" r="5" fill="#fff"/><path d="M1 6h10M6 1c-2 2.5-2 7.5 0 10M6 1c2 2.5 2 7.5 0 10" stroke="var(--teal)" stroke-width="0.8" fill="none"/></svg>
      </div>
    </div>
  </section>
</main>
</body>
</html>
```